eBook Cover - The Quiet Lantern

An eBook cover for a Sci-fi novel along with an Audio Book version.
Specs:
-1x eBook Cover 2,560px x 1,600px (1.5:1 aspect ratio)
-1x Audio Book Cover 3,200px x 3,200px (1:1 aspect ratio) - This should be as minor as possible an alteration from the eBook cover and is not the priority for design choices
Essentials:
-Title: "The Quiet Lantern"
-Author name: "Benedict Harrowe"
-Looks good at a thumbnail size (it is an eBook)
Ideally included:
- Contrast of colours e.g. bright and dark
-Not too many colours, especially if clashing
- A human element e.g. a shadow/outline/shrouded face (I would rather not have a fully visible face as I want this for the readers imagination)
- Gets across that it is sci-fi (and potentially more themes)
-Not too much going on
-Probably not aliens
Potential themes:
-The main civilization's emblem is 3 vertical black rectangles on a white background (please see picture) - I envisage this could in some way be used as a part of the cover, not necessarily black on white etc.
-There is a friendship throughout between two young men, Dorian and Felix, but the main character, Felix, always feels in Dorian's shadow.
-The main character is framed for assassinating an alien ambassador and other characters spend the book trying to find the true killer
-The civilisation is at war, concluding with a battle of space fighters
-Space stations/ships/planets
About the book:
-Humans have colonised across the milky way
-The citizens of the main civilisation (Olundar) believe it is the best civilisation
-It is set in the 23rd Century
-Felix is 23, and is determined, brash and forever trying to prove himself
-Dorian is handsome, likeable, and what Felix wishes he was
-The main locations are a jungle covered planet, space stations and Mars
-They wear white uniforms with black sides
Thanks very much in advance for you time and effort,
Ben

```html
<!DOCTYPE html>
<html lang="en">
<head>
<meta charset="utf-8">
<title>The Quiet Lantern — Benedict Harrowe</title>
<link rel="stylesheet" href="https://fonts.googleapis.com/css2?family=Orbitron:wght@500;700&display=swap">
<style>
  :root {
    --space-deep: #07071a;
    --space-indigo: #2a2a78;
    --nebula-violet: #6a5cc0;
    --nebula-rose: #c8687e;
    --core-glow: #fdf4ea;
    --chrome-light: #ffffff;
    --chrome-mid: #c9c6cf;
    --chrome-dark: #6d6a78;
    --frame-edge: #e6e8f4;
    --blood: #8a0810;
    --blood-deep: #2a0205;
  }
  * { margin: 0; padding: 0; box-sizing: border-box; }
  html, body { width: 750px; height: 1200px; overflow: hidden; background: var(--space-deep); }
  .cover {
    position: relative;
    width: 750px;
    height: 1200px;
    overflow: hidden;
    font-family: "Orbitron", sans-serif;
  }
  .galaxy-art {
    position: absolute;
    inset: 0;
    background:
      radial-gradient(ellipse 230px 90px at 130px 420px, var(--core-glow) 0%, rgba(253,244,234,0.6) 35%, transparent 100%),
      radial-gradient(ellipse 520px 220px at 330px 540px, rgba(200,104,126,0.9) 0%, rgba(106,92,192,0.6) 55%, transparent 100%),
      radial-gradient(ellipse 600px 220px at 420px 330px, rgba(106,92,192,0.55) 0%, transparent 80%),
      radial-gradient(ellipse 520px 200px at 380px 860px, rgba(42,42,120,0.7) 0%, transparent 100%),
      linear-gradient(180deg, var(--space-deep) 0%, #121236 45%, #1b1b55 75%, var(--space-deep) 100%);
  }
  .emblem-frame {
    position: absolute;
    border: 2px solid var(--frame-edge);
    box-shadow: 0 0 6px rgba(255,255,255,0.35), 4px 6px 10px rgba(0,0,0,0.45);
    background:
      linear-gradient(180deg, rgba(210,140,160,0.55) 0%, rgba(160,120,200,0.5) 55%, var(--blood) 82%, var(--blood-deep) 100%);
  }
  .emblem-frame--left   { left: 100px; top: 441px; width: 139px; height: 414px; }
  .emblem-frame--centre { left: 302px; top: 300px; width: 137px; height: 719px;
    background: linear-gradient(180deg, rgba(60,50,90,0.6) 0%, rgba(200,110,130,0.55) 35%, rgba(150,120,210,0.55) 52%, var(--blood-deep) 70%, var(--blood) 88%, var(--blood-deep) 100%); }
  .emblem-frame--right  { left: 508px; top: 468px; width: 139px; height: 338px; }

  .chrome-text {
    position: absolute;
    left: 0;
    width: 100%;
    text-align: center;
    text-transform: uppercase;
    white-space: nowrap;
    line-height: 1;
    font-weight: 500;
    color: transparent;
    background: linear-gradient(180deg, var(--chrome-light) 0%, var(--chrome-mid) 42%, var(--chrome-dark) 52%, var(--chrome-light) 100%);
    -webkit-background-clip: text;
    background-clip: text;
    filter: drop-shadow(0 2px 2px rgba(0,0,0,0.75));
  }
  .title { position: absolute; inset: 0 0 auto 0; height: 260px; font-size: inherit; }
  .title-line--upper {
    top: 58px;
    font-size: 64px;
    letter-spacing: 12px;
    transform: scaleY(1.5);
  }
  .title-line--lower {
    top: 154px;
    font-size: 88px;
    letter-spacing: 10px;
    transform: scaleY(1.7);
  }
  .author {
    top: 1071px;
    font-size: 50px;
    letter-spacing: 0;
    transform: scaleY(1.4);
  }
</style>
</head>
<body>
  <main class="cover">
    <div class="galaxy-art" role="img" aria-label="Swirling spiral galaxy in violet, rose and deep blue with a bright white core, scattered with stars"></div>

    <div class="emblem-frame emblem-frame--left" role="img" aria-label="Tall glass panel showing part of a shadowy male silhouette against the galaxy, with red blood spatter at the base"></div>
    <div class="emblem-frame emblem-frame--centre" role="img" aria-label="Tallest glass panel showing the head of a shadowy male silhouette, fading into a deep red blood pool below"></div>
    <div class="emblem-frame emblem-frame--right" role="img" aria-label="Glass panel showing a silhouetted shoulder with a streak of red blood spatter"></div>

    <h1 class="title">
      <span class="chrome-text title-line--upper">The Quiet</span>
      <span class="chrome-text title-line--lower">Lantern</span>
    </h1>

    <p class="chrome-text author">Benedict Harrowe</p>
  </main>
</body>
</html>
```